Crestline Staffing PEO - Web Build for Professional Employment Organization

We need a website built for our new PEO (professional employment organization). This company will offer third party Human Resource services to companies who are looking to outsource:<br/>Recruiting<br/>Administrative Onboarding<br/>New hire training, ongoing training and development<br/>Payroll/compensation processing/services<br/>Employee Relations<br/>Unemployment Claim Facilitation<br/>Benefits Plans and Administration<br/><br/>I have attached the logo below. Please use that as a reference and color match as best as possible. <br/><br/>Here are some of the competitor's websites:<br/>https://www.velmorahr.com/ <br/>https://www.trundelpay.com/<br/>https://www.trundelpay.com/<br/>https://www.qzn.com/<br/>https://www.bremwickhr.com/<br/>https://orvalepeo.com/contact-orvale/<br/><br/>

Target Market(s)

Startups and mid-sized businesses

Number of Pages Required

5+ page

Font styles to use
Sans Serif

Colors
0592cd

Requirements
Must have
• Features Pages
• SEO driven keyword rich content
• Strong focus on our ability to provide unemployment claim facilitation services as well as mandatory training/certification fulfillment
Nice to have
• I'd like to see one mockup with a Live Chat version if possible. In theory, the Live Chat messages would go directly to our front desk person.

```html
<!DOCTYPE html>
<html lang="en">
<head>
<meta charset="utf-8">
<title>Crestline Staffing PEO</title>
<link href="https://fonts.googleapis.com/css2?family=Exo+2:wght@300;400;500;600;700;800&family=Roboto:wght@400;500;700&display=swap" rel="stylesheet">
<style>
:root{
  --brand:#0592cd;
  --brand-dark:#0b6fb8;
  --teal:#1a9aa8;
  --ink:#25303d;
  --navy:#344157;
  --text:#4e5866;
  --muted:#7a8494;
  --pale:#e6f3fb;
  --band:#1976c8;
  --foot:#1d8bab;
  --star:#f6b40e;
}
*{margin:0;padding:0;box-sizing:border-box}
html,body{width:1200px;height:5115px;overflow:hidden}
body{font-family:"Roboto",sans-serif;color:var(--text);background:#fff;position:relative}
.abs{position:absolute}
h1,h2,h3,h4,.head{font-family:"Exo 2",sans-serif}
.bar{width:64px;height:3px;background:var(--brand)}
.btn{display:flex;align-items:center;justify-content:center;background:var(--brand-dark);color:#fff;font:600 13px "Exo 2",sans-serif;letter-spacing:.4px;text-transform:uppercase;border-radius:2px}

/* header + hero */
.hero{left:0;top:0;width:1200px;height:719px;background:linear-gradient(100deg,#f1f5f7 0%,#e6ecef 35%,#d8dcdc 55%,#c9bfb3 75%,#b7c2c9 100%)}
.logo{left:143px;top:36px;font:700 36px/1 "Exo 2",sans-serif;color:#1e5f9c;letter-spacing:.5px}
.logo small{display:block;font-size:16px;letter-spacing:7px;margin-top:6px;padding-left:4px}
.callnow{left:584px;top:26px;display:flex;gap:10px;align-items:center}
.callnow .ic{width:40px;height:40px;border-radius:50%;border:2px solid #6c7480;display:flex;align-items:center;justify-content:center}
.callnow p{font:500 12px "Roboto",sans-serif;color:#333}
.callnow b{display:block;font:600 21px "Exo 2",sans-serif;color:var(--teal)}
.auth{top:32px;height:34px;border-radius:4px;font:600 12px "Roboto",sans-serif;display:flex;align-items:center;justify-content:center;gap:6px}
.login{left:832px;width:96px;border:1px solid #555;color:#333;background:#fff}
.signup{left:948px;width:107px;background:var(--brand);color:#fff}
.nav{top:94px;left:526px;display:flex;gap:26px;font:600 14px "Exo 2",sans-serif;color:#2d3540}
.nav .on{color:var(--brand);position:relative}
.nav .on:after{content:"";position:absolute;left:0;right:0;bottom:-28px;height:2px;background:var(--brand)}
.hero-title{left:143px;top:262px;font:700 47px/55px "Exo 2",sans-serif;color:#374251;letter-spacing:.3px}
.hero-title em{font-style:normal;color:var(--brand-dark);font-weight:800}
.arrow{top:394px;width:32px;height:32px;border-radius:50%;background:#3b3f44;display:flex;align-items:center;justify-content:center}

/* welcome */
.welcome{left:0;top:719px;width:1200px;text-align:center}
.welcome h3{margin-top:72px;font:400 22px "Exo 2",sans-serif;color:#333}
.welcome h2{font:700 36px "Exo 2",sans-serif;color:#1f2730;margin-top:4px}
.welcome .bar{margin:12px auto 0;background:#1f2730}
.welcome p{width:810px;margin:32px auto 0;font-size:14px;line-height:26px}
.pillar{top:1088px;width:296px;height:252px;background:linear-gradient(180deg,#e3f1fa 0%,#fff 60%);box-shadow:0 2px 8px rgba(0,0,0,.08);padding:16px 26px}
.pillar .row{display:flex;align-items:center;gap:14px}
.pillar .cir{width:74px;height:74px;border-radius:50%;background:var(--teal);display:flex;align-items:center;justify-content:center}
.pillar h4{font:600 17px "Exo 2",sans-serif;color:#1f2730}
.pillar p{margin-top:18px;font-size:13.5px;line-height:24px}

/* services */
.svc-band{left:0;top:1438px;width:1200px;height:474px;background:linear-gradient(120deg,#1a84d4,#1565b8 60%,#1a7fcf)}
.svc-title{left:0;top:1502px;width:1200px;text-align:center;color:#fff;font:700 38px/47px "Exo 2",sans-serif}
.svc-title .bar{background:#fff;margin:14px auto 0}
.svc{width:221px;height:316px;background:#fff;box-shadow:0 3px 10px rgba(0,0,0,.12);text-align:center;padding-top:36px}
.svc.lower{border-top:3px solid var(--brand-dark)}
.svc .cir{width:92px;height:92px;margin:0 auto;border-radius:50%;border:3px solid var(--brand-dark);display:flex;align-items:center;justify-content:center}
.svc .cir span{width:74px;height:74px;border-radius:50%;background:var(--brand-dark);display:flex;align-items:center;justify-content:center}
.svc h4{margin-top:20px;font:500 17px/23px "Exo 2",sans-serif;color:#222}
.svc p{margin:8px auto 0;width:184px;font-size:13.5px;line-height:24px}

/* claim */
.claim{left:0;top:2400px;width:1200px;height:603px;background:linear-gradient(180deg,#fff 0%,#f3f8fd 55%,#dcecf9 100%)}
.claim-art{left:520px;top:2425px;width:642px;height:478px;border-radius:48% 40% 44% 50%;background:radial-gradient(circle at 60% 45%,#9ec6f2,#d2e5f7 55%,#edf4fb 80%)}

/* testimonials */
.voices{left:0;top:3003px;width:1200px;height:643px;background:linear-gradient(120deg,#1c9fb0,#177f9e 60%,#1a93aa)}
.quote-card{left:441px;top:3297px;width:328px;height:278px;background:#fff}
.avatar{width:176px;height:176px;border-radius:50%;border:3px solid #fff;background:linear-gradient(160deg,#c9d3dc,#6d7b88)}
.person{width:300px;text-align:center}
.person h4{font:500 17px "Exo 2",sans-serif}
.person small{display:block;font:500 11px "Roboto",sans-serif;margin-top:5px}
.person p{font-size:13px;line-height:23px;margin-top:14px;padding:0 20px}
.person .stars{margin-top:16px;color:var(--star);font-size:15px;letter-spacing:3px}
.light{color:#e1f3f6}
.light h4{color:#fff}
.dark h4{color:#222}.dark small{color:#333}

/* news */
.post{top:3853px;width:276px;height:366px;background:#fff;box-shadow:0 2px 10px rgba(0,0,0,.12)}
.post .ph{margin:8px 8px 0;height:176px}
.post .body{padding:18px 22px}
.post .date{font:600 13px "Roboto",sans-serif;color:#222;display:flex;gap:8px;align-items:center}
.post h4{margin-top:14px;font:700 13px/22px "Roboto",sans-serif;color:var(--brand-dark)}
.post p{margin-top:12px;font-size:12.5px;line-height:22px}

/* contact + footer */
.contact-bg{left:0;top:4270px;width:1200px;height:642px}
.form{left:139px;top:4344px;width:356px;height:488px;background:#fff;box-shadow:0 4px 16px rgba(0,0,0,.18);padding:30px 26px}
.form h3{font:700 27px "Exo 2",sans-serif;color:#1f2730}
.form .lead{margin-top:6px;font:500 12.5px/20px "Roboto",sans-serif;color:#222}
.field{margin-top:12px;height:36px;border:1px solid #d5dade;background:#f7f8f9;font-size:11px;color:#777;padding:11px 12px}
.field.big{height:80px}
.form .btn{margin-top:18px;height:40px;background:var(--brand-dark);font-size:14px}
.foot-brand{left:558px;top:4496px;font:700 38px/1 "Exo 2",sans-serif;color:#fff}
.foot-brand small{display:block;font-size:18px;letter-spacing:8px;margin-top:4px;padding-left:110px}
.foot-about{left:558px;top:4580px;width:500px;font-size:13.5px;line-height:20px;color:#d6dde6}
.info{left:558px;display:flex;gap:20px;align-items:center;color:#e4e9ef;font-size:13px;line-height:20px}
.info .ic{width:40px;height:40px;border-radius:50%;border:2px solid #fff;display:flex;align-items:center;justify-content:center;flex:none}
.chat{left:910px;top:4862px;width:254px;height:48px;background:var(--brand);display:flex;align-items:center;padding:0 20px 0 24px;color:#fff;font:700 13px "Exo 2",sans-serif;letter-spacing:.4px;gap:10px;border-radius:3px 3px 0 0}
.chat .x{margin-left:auto;font:700 18px "Roboto",sans-serif}
.bottom{left:0;top:4910px;width:1200px;height:205px;background:var(--foot);text-align:center;color:#fff}
.bottom .links{margin-top:50px;font:500 14px "Roboto",sans-serif;word-spacing:2px}
.bottom .copy{margin-top:22px;font-size:14px}
.socials{margin-top:20px;display:flex;gap:6px;justify-content:center}
.socials span{width:28px;height:28px;border-radius:50%;border:1.5px solid #fff}
</style>
</head>
<body>

<!-- header / hero -->
<section class="abs hero" role="img" aria-label="Photo of a smiling woman working on a laptop in a bright room with a plant on a side table"></section>
<div class="abs logo">Crestline Staffing<small>PEO</small></div>
<div class="abs callnow">
  <div class="ic"><svg width="18" height="18" viewBox="0 0 24 24"><path d="M6.6 10.8a15 15 0 0 0 6.6 6.6l2.2-2.2c.3-.3.7-.4 1-.2 1.1.4 2.3.6 3.6.6.6 0 1 .4 1 1V20c0 .6-.4 1-1 1A17 17 0 0 1 3 4c0-.6.4-1 1-1h3.5c.6 0 1 .4 1 1 0 1.3.2 2.5.6 3.6.1.3 0 .7-.2 1z" fill="#555"/></svg></div>
  <p>Call Now<b>808.4170.2286</b></p>
</div>
<div class="abs auth login"><svg width="10" height="11" viewBox="0 0 10 11"><rect x="1" y="5" width="8" height="6" fill="#333"/><path d="M3 5V3a2 2 0 0 1 4 0v2" stroke="#333" fill="none" stroke-width="1.4"/></svg>LOGIN</div>
<div class="abs auth signup"><svg width="11" height="11" viewBox="0 0 11 11"><path d="M1 10l1-3 6-6 2 2-6 6z" fill="#fff"/></svg>SIGN UP</div>
<nav class="abs nav"><span class="on">HOME</span><span>ABOUT US</span><span>OUR SERVICES</span><span>TEAM</span><span>BLOG</span><span>CONTACT US</span></nav>
<h1 class="abs hero-title">PROFESSIONAL<br><em>EMPLOYMENT</em><br>ORGANIZATION</h1>
<div class="abs btn" style="left:143px;top:443px;width:221px;height:42px">Explore HR Solutions</div>
<div class="abs arrow" style="left:70px"><svg width="12" height="12" viewBox="0 0 12 12"><path d="M8 1L3 6l5 5" stroke="#fff" stroke-width="2" fill="none"/></svg></div>
<div class="abs arrow" style="left:1096px"><svg width="12" height="12" viewBox="0 0 12 12"><path d="M4 1l5 5-5 5" stroke="#fff" stroke-width="2" fill="none"/></svg></div>

<!-- welcome -->
<section class="abs welcome">
  <h3>WELCOME TO</h3>
  <h2>CRESTLINE STAFFING PEO</h2>
  <div class="bar"></div>
  <p>Sed ut perspiciatis unde omnis iste natus error sit voluptatem accusantium doloremque laudantium, totam rem aperiam, eaque ipsa quae ab illo inventore veritatis et quasi architecto beatae vitae dicta sunt explicabo. Nemo enim ipsam voluptatem quia voluptas sit aspernatur aut odit aut fugit, sed quia consequuntur magni dolores eos qui ratione voluptatem sequi nesciunt. Neque porro quisquam est, qui dolorem ipsum quia dolor sit amet, consectetur, adipisci velit, sed quia non numquam eius modi tempora incidunt ut labore et dolore magnam</p>
</section>
<div class="abs pillar" style="left:143px"><div class="row"><div class="cir"><svg width="36" height="36" viewBox="0 0 36 36" fill="none" stroke="#fff" stroke-width="2"><circle cx="18" cy="18" r="5"/><circle cx="7" cy="8" r="3"/><circle cx="29" cy="8" r="3"/><circle cx="7" cy="28" r="3"/><circle cx="29" cy="28" r="3"/><path d="M9 10l5 5M27 10l-5 5M9 26l5-5M27 26l-5-5"/></svg></div><h4>CONNECT</h4></div><p>Sed ut perspiciatis unde omnis iste natus error sit voluptatem accutium doloremque laudantium, totam rem aperiam, eaque ipsa quae ab illo tatis et quasi architecto beatae</p></div>
<div class="abs pillar" style="left:451px"><div class="row"><div class="cir"><svg width="36" height="36" viewBox="0 0 36 36" fill="none" stroke="#fff" stroke-width="2"><path d="M4 20l8-6 6 4 6-4 8 6-8 8-6-4-6 4z"/><circle cx="18" cy="9" r="4"/></svg></div><h4>MEET</h4></div><p>Sed ut perspiciatis unde omnis iste natus error sit voluptatem accutium doloremque laudantium, totam rem aperiam, eaque ipsa quae ab illo tatis et quasi architecto beatae</p></div>
<div class="abs pillar" style="left:758px"><div class="row"><div class="cir"><svg width="36" height="36" viewBox="0 0 36 36" fill="none" stroke="#fff" stroke-width="2"><path d="M6 30l10-10 5 5 10-15"/><path d="M24 10h7v7"/></svg></div><h4>ELEVATE</h4></div><p>Sed ut perspiciatis unde omnis iste natus error sit voluptatem accutium doloremque laudantium, totam rem aperiam, eaque ipsa quae ab illo tatis et quasi architecto beatae</p></div>

<!-- services -->
<section class="abs svc-band"></section>
<h2 class="abs svc-title">OUR FULL SERVICE<br>HR SOLUTION DELIVERS<div class="bar"></div></h2>

<div class="abs svc" style="left:143px;top:1668px"><div class="cir"><span><svg width="36" height="36" viewBox="0 0 36 36" fill="none" stroke="#fff" stroke-width="2"><rect x="8" y="6" width="16" height="22"/><path d="M12 12h8M12 17h8M12 22h5"/><circle cx="25" cy="24" r="5"/><path d="M29 28l4 4"/></svg></span></div><h4>Recruiting</h4><p>Sed ut perspiciatis unde omnis iste natus voluptatem accusantium doloremque um, totam rem aperiam</p></div>
<div class="abs svc" style="left:373px;top:1668px"><div class="cir"><span><svg width="36" height="36" viewBox="0 0 36 36" fill="none" stroke="#fff" stroke-width="2"><circle cx="18" cy="12" r="6"/><path d="M7 31c0-7 5-11 11-11s11 4 11 11"/></svg></span></div><h4>Administrative<br>Onboarding</h4><p>Sed ut perspiciatis unde omnis iste natus voluptatem accusantium doloremque um, totam rem aperiam</p></div>
<div class="abs svc" style="left:604px;top:1668px"><div class="cir"><span><svg width="36" height="36" viewBox="0 0 36 36" fill="none" stroke="#fff" stroke-width="2"><rect x="5" y="6" width="26" height="16"/><path d="M10 18l6-5 4 3 6-6"/><circle cx="11" cy="28" r="2"/><circle cx="18" cy="28" r="2"/><circle cx="25" cy="28" r="2"/></svg></span></div><h4>New hire training</h4><p>Sed ut perspiciatis unde omnis iste natus voluptatem accusantium doloremque um, totam rem aperiam</p></div>
<div class="abs svc" style="left:834px;top:1668px"><div class="cir"><span><svg width="36" height="36" viewBox="0 0 36 36" fill="none" stroke="#fff" stroke-width="2"><rect x="6" y="6" width="24" height="16"/><circle cx="18" cy="14" r="3"/><circle cx="9" cy="28" r="2.5"/><circle cx="18" cy="28" r="2.5"/><circle cx="27" cy="28" r="2.5"/></svg></span></div><h4>Ongoing training</h4><p>Sed ut perspiciatis unde omnis iste natus voluptatem accusantium doloremque um, totam rem aperiam</p></div>

<div class="abs svc lower" style="left:143px;top:2002px"><div class="cir"><span><svg width="36" height="36" viewBox="0 0 36 36" fill="none" stroke="#fff" stroke-width="2"><rect x="7" y="5" width="18" height="26"/><path d="M11 11h10M11 16h10M11 21h6"/><circle cx="27" cy="24" r="5"/><path d="M27 21v6"/></svg></span></div><h4>Payroll</h4><p>Sed ut perspiciatis unde omnis iste natus voluptatem accusantium doloremque um, totam rem aperiam</p></div>
<div class="abs svc lower" style="left:373px;top:2002px"><div class="cir"><span><svg width="36" height="36" viewBox="0 0 36 36" fill="none" stroke="#fff" stroke-width="2"><rect x="6" y="7" width="24" height="18"/><circle cx="14" cy="15" r="3"/><path d="M20 13h6M20 18h6M12 31h12"/></svg></span></div><h4>Unemployment<br>Claim Facilitation</h4><p>Sed ut perspiciatis unde omnis iste natus voluptatem accusantium doloremque um, totam rem aperiam</p></div>
<div class="abs svc lower" style="left:604px;top:2002px"><div class="cir"><span><svg width="36" height="36" viewBox="0 0 36 36" fill="none" stroke="#fff" stroke-width="2"><circle cx="18" cy="9" r="4"/><circle cx="8" cy="22" r="3.5"/><circle cx="28" cy="22" r="3.5"/><path d="M18 13v6M14 19h8M3 32c0-3 2-5 5-5s5 2 5 5M23 32c0-3 2-5 5-5s5 2 5 5"/></svg></span></div><h4>Employee Relations</h4><p>Sed ut perspiciatis unde omnis iste natus voluptatem accusantium doloremque um, totam rem aperiam</p></div>
<div class="abs svc lower" style="left:834px;top:2002px"><div class="cir"><span><svg width="36" height="36" viewBox="0 0 36 36" fill="none" stroke="#fff" stroke-width="2"><path d="M18 4l12 5v8c0 8-5 13-12 15C11 30 6 25 6 17V9z"/><path d="M12 18l4 4 8-8"/></svg></span></div><h4>Benefits Plans<br>and Administration</h4><p>Sed ut perspiciatis unde omnis iste natus voluptatem accusantium doloremque um, totam rem aperiam</p></div>

<!-- claim -->
<section class="abs claim"></section>
<div class="abs claim-art" role="img" aria-label="Isometric illustration of a laptop showing a star-rated profile, a magnifying glass, a potted plant and a small figure reviewing claim cards"></div>
<h2 class="abs" style="left:143px;top:2480px;font:300 37px/46px 'Exo 2',sans-serif;color:#1f2730">Unemployment<b style="display:block;font-weight:600">Claim Facilitation</b></h2>
<div class="abs bar" style="left:143px;top:2593px"></div>
<p class="abs" style="left:143px;top:2622px;width:648px;font-size:14px;line-height:24px">Sed ut perspiciatis unde omnis iste natus error sit<br>voluptatem accusantium doloremque laudantium, totam<br>rem aperiam, eaque ipsa quae ab illo inventore veritatis et<br>quasi architecto beatae vitae dicta sunt explicabo. Nemo<br>enim ipsam voluptatem quia voluptas sit aspernatur aut<br>odit aut fugit, sed quia consequuntur magni dolores eos qui<br>ratione voluptatem sequi nesciunt.</p>
<div class="abs btn" style="left:143px;top:2822px;width:222px;height:44px">Explore HR Solutions</div>

<!-- testimonials -->
<section class="abs voices"></section>
<h2 class="abs" style="left:0;top:3073px;width:1200px;text-align:center;color:#fff;font:700 31px/38px 'Exo 2',sans-serif">SEE WHAT OUR CLIENTS ARE<br>SAYING ABOUT US</h2>
<div class="abs quote-card"></div>
<div class="abs avatar" style="left:188px;top:3193px" role="img" aria-label="Portrait photo of client Marcus Ellwood"></div>
<div class="abs avatar" style="left:516px;top:3193px" role="img" aria-label="Portrait photo of client Owen Tarrant"></div>
<div class="abs avatar" style="left:834px;top:3193px" role="img" aria-label="Portrait photo of client Julian Pryce"></div>
<div class="abs person light" style="left:126px;top:3390px"><h4>Marcus Ellwood</h4><small>Founder &amp; General</small><p>Sed ut perspiciatis unde omnis iste natus error sit voluptatem accusantium doloremque laudantium</p><div class="stars">★★★★☆</div></div>
<div class="abs person dark" style="left:455px;top:3390px"><h4>Owen Tarrant</h4><small>Information &amp; Knowledge</small><p>Sed ut perspiciatis unde omnis iste natus error sit voluptatem accusantium doloremque laudantium</p><div class="stars">★★★★☆</div></div>
<div class="abs person light" style="left:774px;top:3390px"><h4>Julian Pryce</h4><small>Content Manager</small><p>Sed ut perspiciatis unde omnis iste natus error sit voluptatem accusantium doloremque laudantium</p><div class="stars">★★★★☆</div></div>

<!-- news -->
<h2 class="abs" style="left:0;top:3748px;width:1200px;text-align:center;font:700 36px 'Exo 2',sans-serif;color:#1f2730">LATEST NEWS</h2>
<div class="abs bar" style="left:568px;top:3805px;background:var(--brand-dark)"></div>
<article class="abs post" style="left:145px"><div class="ph" role="img" aria-label="Photo of hands on a laptop beside a dark join-us banner" style="background:linear-gradient(120deg,#e88a3b 0%,#2a3440 45%,#151c24 100%)"></div><div class="body"><div class="date"><svg width="12" height="12" viewBox="0 0 12 12"><rect x="1" y="2" width="10" height="9" fill="none" stroke="#333" stroke-width="1.4"/><path d="M1 5h10" stroke="#333"/></svg>JAN 23, 2020</div><h4>NEMO ENIM IPSAM VOLUP<br>QUIA VOLUPTAS SIT</h4><p>Sed ut perspiciatis unde omnis iste natus error sit voluptatem accuntium domque laudantium, totam</p></div></article>
<article class="abs post" style="left:463px"><div class="ph" role="img" aria-label="Photo of a hand holding a glowing network of people icons" style="background:linear-gradient(160deg,#3a5f8a,#1a2f4d 70%)"></div><div class="body"><div class="date"><svg width="12" height="12" viewBox="0 0 12 12"><rect x="1" y="2" width="10" height="9" fill="none" stroke="#333" stroke-width="1.4"/><path d="M1 5h10" stroke="#333"/></svg>JAN 23, 2020</div><h4>NEMO ENIM IPSAM VOLUP<br>QUIA VOLUPTAS SIT</h4><p>Sed ut perspiciatis unde omnis iste natus error sit voluptatem accuntium domque laudantium, totam</p></div></article>
<article class="abs post" style="left:781px"><div class="ph" role="img" aria-label="Photo of colleagues talking in a modern office" style="background:linear-gradient(120deg,#3c3a38,#8a6a4e 55%,#d19a52)"></div><div class="body"><div class="date"><svg width="12" height="12" viewBox="0 0 12 12"><rect x="1" y="2" width="10" height="9" fill="none" stroke="#333" stroke-width="1.4"/><path d="M1 5h10" stroke="#333"/></svg>JAN 23, 2020</div><h4>NEMO ENIM IPSAM VOLUP<br>QUIA VOLUPTAS SIT</h4><p>Sed ut perspiciatis unde omnis iste natus error sit voluptatem accuntium domque laudantium, totam</p></div></article>

<!-- contact + footer -->
<svg class="abs contact-bg" viewBox="0 0 1200 642" preserveAspectRatio="none"><polygon points="0,222 1200,100 1200,642 0,642" fill="#344157"/></svg>
<div class="abs form">
  <h3>CONTACT US TODAY</h3>
  <p class="lead">Fill Out the Form Below &nbsp;or Call Crestline Staffing PEO at (808) 3146-7720</p>
  <div class="field">Name</div>
  <div class="field">Email address</div>
  <div class="field">Phone</div>
  <div class="field">Subjects</div>
  <div class="field big">Message</div>
  <div class="btn">Submit</div>
</div>
<div class="abs foot-brand">Crestline Staffing<small>PEO</small></div>
<p class="abs foot-about">Sed ut perspiciatis unde omnis iste natus sit voluptatem accusantium doloremque laudantium, totam rem aperiam, eaque ipsa</p>
<div class="abs info" style="top:4636px"><span class="ic"><svg width="16" height="18" viewBox="0 0 16 18"><path d="M8 17s6-6 6-10A6 6 0 0 0 2 7c0 4 6 10 6 10z" fill="none" stroke="#fff" stroke-width="1.6"/><circle cx="8" cy="7" r="2" fill="#fff"/></svg></span><span>14 Harlow Yard, Brenmoor, Ashvale,<br>AV7 2QT</span></div>
<div class="abs info" style="top:4698px"><span class="ic"><svg width="16" height="16" viewBox="0 0 24 24"><path d="M6.6 10.8a15 15 0 0 0 6.6 6.6l2.2-2.2c.3-.3.7-.4 1-.2 1.1.4 2.3.6 3.6.6.6 0 1 .4 1 1V20c0 .6-.4 1-1 1A17 17 0 0 1 3 4c0-.6.4-1 1-1h3.5c.6 0 1 .4 1 1 0 1.3.2 2.5.6 3.6.1.3 0 .7-.2 1z" fill="#fff"/></svg></span><span>Call Us :<br>(808) 3146 - 7720</span></div>
<div class="abs info" style="top:4760px"><span class="ic"><svg width="18" height="14" viewBox="0 0 18 14"><rect x="1" y="1" width="16" height="12" fill="none" stroke="#fff" stroke-width="1.6"/><path d="M1 1l8 7 8-7" fill="none" stroke="#fff" stroke-width="1.6"/></svg></span><span>E - Mail :<br>info@crestlinestaffingpeo.com</span></div>
<div class="abs chat"><svg width="16" height="14" viewBox="0 0 16 14"><path d="M2 1h12v8H7l-4 3V9H2z" fill="#fff"/></svg>LIVE CHAT SUPPORT<span class="x">✕</span></div>
<footer class="abs bottom">
  <p class="links">Home &nbsp;| &nbsp;About Us &nbsp;| &nbsp;Our Services &nbsp;| &nbsp;Team &nbsp;| &nbsp;Blog &nbsp;| &nbsp;Contact Us</p>
  <p class="copy">© 2020 Crestline Staffing PEO . All rights reserved. Privacy Policy</p>
  <div class="socials"><span></span><span></span><span></span><span></span></div>
</footer>
</body>
</html>
```